Allied Health team of Physiotherapists & Occupational Therapists seek a business card design

We have our new logo, we now need our new business cards and stationary. Tidewell: Oedema & Family Clinic is seeking a generic card design to represent our whole team and individual cards for each therapist that incorporates our new logo to communicate our holistic approach that is calming, nuturing, supportive and welcoming.
Our Physiotherapists and Occupational Therapists assess, treat and provide education for people who are at risk of or who have lymphoedema. This is often as a result of treatment for cancer. We provide pre-operative and post-operative management and cancer rehabilitation in our Pilates studio. Our team also consists of Physiotherapists who have a strong interest in pelvic floor and continence management for both men and women.

Target Market(s)

Mainly women health conscious

Industry/Entity Type

Allied Health: Physiotherapy / Occupational Therapy

Contact Information for Business Card

Address: 14 Gallivant Ave Frankston 3199 Phone: 84316570 fax: 8431 6578 Email: info@tidewellcareservices.com.au Website: tidewellcareservices.com.au Facebook address: facebook.com/TidewellOedemaAndFamilyCareClinic. Room to write appointments. Individual cards need to have name, office email and individual email and professional details

Requirements
Must have
• Logo as per uploaded documents

```html
<!DOCTYPE html>
<html lang="en">
<head>
<meta charset="utf-8">
<title>Tidewell Business Cards</title>
<link rel="stylesheet" href="https://fonts.googleapis.com/css2?family=Arimo&family=Josefin+Sans:wght@400&display=swap">
<style>
  :root {
    --stage: #6a6a6a;
    --ink-dark: #252525;
    --cream: #fcf9dc;
    --peach: #f7c4a0;
    --peach-text: #f0a878;
    --light-text: #f4f1e6;
  }
  * { box-sizing: border-box; margin: 0; padding: 0; }
  html, body { width: 1200px; height: 1015px; overflow: hidden; }
  body {
    background: var(--stage);
    font-family: "Arimo", Arial, sans-serif;
    position: relative;
  }
  .card {
    position: absolute;
    left: 250px;
    width: 700px;
    height: 400px;
    overflow: hidden;
    background: var(--ink-dark);
    box-shadow: 0 10px 30px rgba(0,0,0,.35);
  }
  .card--contact { top: 85px; }
  .card--profile { top: 530px; }
  .card__wave { position: absolute; inset: 0; width: 100%; height: 100%; }
  .card--profile .card__wave { transform: rotate(180deg); }

  .brand {
    position: absolute;
    display: flex;
    align-items: center;
    gap: 12px;
    color: var(--peach-text);
    font-size: 34px;
    line-height: 1;
    letter-spacing: 1px;
    white-space: nowrap;
  }
  .brand__dot {
    width: 18px; height: 18px;
    border-radius: 50%;
    background: var(--peach);
  }
  .card--contact .brand { right: 50px; top: 240px; }
  .card--profile .brand { left: 50px; top: 124px; }

  .contact-list {
    position: absolute;
    left: 44px; top: 70px;
    list-style: none;
    color: var(--light-text);
    font-size: 16px;
    line-height: 1.55;
  }
  .contact-list li { display: flex; align-items: center; gap: 10px; }
  .contact-list svg { width: 16px; height: 16px; flex: none; }

  .profile {
    position: absolute;
    right: 40px; top: 140px;
    text-align: right;
    color: var(--light-text);
    font-size: 15px;
    line-height: 1.45;
  }
  .profile__name {
    font-family: "Josefin Sans", Arial, sans-serif;
    font-weight: 400;
    color: var(--peach-text);
    font-size: 26px;
    letter-spacing: 3px;
    margin-bottom: 8px;
  }
  .profile__roles { margin-top: 14px; }
</style>
</head>
<body>

<section class="card card--contact" aria-label="Contact side of business card">
  <svg class="card__wave" viewBox="0 0 700 400" preserveAspectRatio="none" aria-hidden="true">
    <path d="M700,15 C570,15 505,80 462,170 C410,285 320,378 150,400 L700,400 Z" fill="var(--peach)"/>
    <path d="M700,40 C580,40 522,100 482,180 C432,290 340,380 178,400 L700,400 Z" fill="var(--cream)"/>
  </svg>
  <div class="brand"><span class="brand__dot"></span>Tidewell</div>
  <ul class="contact-list">
    <li>
      <svg viewBox="0 0 16 16"><path d="M3 1.5l3 3-1.5 2c1 2 2.5 3.5 4.5 4.5l2-1.5 3 3-2 2C6 14 2 10 1.5 3.5z" fill="var(--peach-text)"/></svg>
      000 5555 6666
    </li>
    <li>
      <svg viewBox="0 0 16 16"><rect x="1" y="3" width="14" height="10" fill="var(--peach-text)"/><path d="M1 3l7 6 7-6" fill="none" stroke="var(--ink-dark)" stroke-width="1.3"/></svg>
      info@tidewellcareservices.com.au
    </li>
    <li>
      <svg viewBox="0 0 16 16"><rect x="1" y="3" width="14" height="10" fill="var(--peach-text)"/><path d="M1 3l7 6 7-6" fill="none" stroke="var(--ink-dark)" stroke-width="1.3"/></svg>
      name@tidewellcareservices.com.au
    </li>
    <li>
      <svg viewBox="0 0 16 16"><g fill="none" stroke="var(--peach-text)" stroke-width="1.4"><circle cx="8" cy="8" r="6.5"/><ellipse cx="8" cy="8" rx="3" ry="6.5"/><path d="M1.5 8h13M2.5 4.8h11M2.5 11.2h11"/></g></svg>
      www.tidewellcareservices.com.au
    </li>
  </ul>
</section>

<section class="card card--profile" aria-label="Profile side of business card">
  <svg class="card__wave" viewBox="0 0 700 400" preserveAspectRatio="none" aria-hidden="true">
    <path d="M700,15 C570,15 505,80 462,170 C410,285 320,378 150,400 L700,400 Z" fill="var(--peach)"/>
    <path d="M700,40 C580,40 522,100 482,180 C432,290 340,380 178,400 L700,400 Z" fill="var(--cream)"/>
  </svg>
  <div class="brand"><span class="brand__dot"></span>Tidewell</div>
  <div class="profile">
    <h1 class="profile__name">MAREN HOLLOWAY</h1>
    <p>B. Physio (Hons), B.App.Sci.(Human Movement/Psych)</p>
    <p>Post Grad Certif. Exercise for Women</p>
    <p>Post Grad Certif. Continence &amp; Pelvic Floor Rehabilitation</p>
    <div class="profile__roles">
      <p>Physiotherapist</p>
      <p>Lymphoedema &amp; Oncology Rehabilitation</p>
      <p>Continence &amp; Pelvic Floor</p>
    </div>
  </div>
</section>

</body>
</html>
```